New Business card design to reflect rebrand

I would like a business card design with a good base colour for our new logo and also a placeholder for a profile pic of the card holder. the design needs to be editable to the point that we can easily change the picture of the person and use that design for printmerlo etc. we are looking at a metalic finish business card so will need a good base colour to bring out the finish.

Target Market(s)

prospective customers

Industry/Entity Type

Business

Contact Information for Business Card

I would like one editable design that we can change the name of the card holder and profile picture. The design need to be in a format that be send to printmerlo etc.

Our address is Fenwick Lodge, Copse Lane, Ashcombe Vale, GU14 3TP Tel no. 01483 556172

Requirements
Must have
• place holder for a profile pic for the card holder. in AI or preferably PSD format

```html
<!DOCTYPE html>
<html lang="en">
<head>
<meta charset="utf-8">
<title>Brightmere Workplace Services – Business Card</title>
<link rel="stylesheet" href="https://fonts.googleapis.com/css2?family=Open+Sans:wght@400;600;700&display=swap">
<style>
  :root {
    --navy: #3f566f;
    --navy-light: #4d6784;
    --navy-dark: #34485e;
    --orange: #e5670f;
    --paper: #ffffff;
    --ink: #4a4a4a;
    --photo: #9b9b9b;
    --stage: #e9e6e1;
  }
  * { box-sizing: border-box; margin: 0; padding: 0; }
  html, body { width: 1200px; height: 843px; overflow: hidden; }
  body {
    background: var(--stage);
    font-family: "Open Sans", Arial, sans-serif;
    position: relative;
  }
  .card {
    position: absolute;
    top: 246px;
    width: 540px;
    height: 350px;
    border-radius: 4px;
    overflow: hidden;
    box-shadow: 0 10px 28px rgba(0,0,0,0.18);
  }

  /* Back side */
  .card--back {
    left: 40px;
    background: linear-gradient(160deg, var(--navy-light), var(--navy-dark));
  }
  .card--back .brand {
    position: absolute;
    left: 0; right: 0; top: 140px;
    text-align: center;
    color: var(--paper);
  }
  .card--back .brand-name {
    font-size: 40px;
    font-weight: 700;
    letter-spacing: 2px;
    line-height: 1;
  }
  .card--back .brand-tag {
    margin-top: 8px;
    font-size: 15px;
    font-weight: 700;
    letter-spacing: 4px;
  }
  .card--back .web {
    position: absolute;
    left: 0; right: 0; bottom: 30px;
    text-align: center;
    font-size: 13px;
    letter-spacing: 3px;
    color: rgba(255,255,255,0.8);
  }

  /* Front side */
  .card--front {
    left: 620px;
    background: var(--paper);
  }
  .front-art {
    position: absolute;
    inset: 0;
    width: 540px;
    height: 350px;
  }
  .card--front .brand {
    position: absolute;
    left: 48px; top: 30px;
    color: var(--navy);
  }
  .card--front .brand-name {
    font-size: 30px;
    font-weight: 700;
    letter-spacing: 1.5px;
    line-height: 1;
  }
  .card--front .brand-tag {
    margin-top: 5px;
    font-size: 11.5px;
    font-weight: 700;
    letter-spacing: 3px;
  }
  .holder {
    position: absolute;
    left: 48px; top: 112px;
  }
  .holder::before {
    content: "";
    position: absolute;
    left: -48px; top: 2px;
    width: 14px; height: 38px;
    background: var(--navy);
  }
  .holder-name {
    font-size: 19px;
    font-weight: 600;
    color: var(--navy);
    line-height: 1.2;
  }
  .holder-role {
    font-size: 14px;
    color: var(--orange);
    line-height: 1.3;
  }
  .address {
    position: absolute;
    left: 48px; top: 176px;
    font-style: normal;
    font-size: 13px;
    line-height: 1.45;
    color: var(--ink);
  }
  .phone {
    position: absolute;
    left: 48px; top: 250px;
    display: flex;
    align-items: center;
    gap: 8px;
    font-size: 14px;
    color: var(--ink);
  }
  .phone svg { width: 12px; height: 12px; fill: var(--orange); }
</style>
</head>
<body>

  <section class="card card--back" aria-label="Card back">
    <div class="brand">
      <div class="brand-name">BRIGHTMERE</div>
      <div class="brand-tag">WORKPLACE SERVICES</div>
    </div>
    <div class="web">www.brightmere.co.uk</div>
  </section>

  <section class="card card--front" aria-label="Card front">
    <svg class="front-art" viewBox="0 0 540 350" preserveAspectRatio="none">
      <polygon points="470,0 540,0 540,350 420,350" fill="var(--orange)"/>
      <rect role="img" aria-label="Profile photo of the card holder"
            x="262" y="90" width="200" height="260" fill="var(--photo)"/>
    </svg>

    <div class="brand">
      <div class="brand-name">BRIGHTMERE</div>
      <div class="brand-tag">WORKPLACE SERVICES</div>
    </div>

    <div class="holder">
      <div class="holder-name">Tom Archer</div>
      <div class="holder-role">CEO/Founder</div>
    </div>

    <address class="address">
      Fenwick Lodge<br>
      Copse Lane, Ashcombe Vale<br>
      GU14 3TP
    </address>

    <div class="phone">
      <svg viewBox="0 0 24 24" aria-hidden="true"><path d="M6.6 10.8a15.1 15.1 0 0 0 6.6 6.6l2.2-2.2a1 1 0 0 1 1-.25 11.4 11.4 0 0 0 3.6.57 1 1 0 0 1 1 1V20a1 1 0 0 1-1 1A17 17 0 0 1 3 4a1 1 0 0 1 1-1h3.5a1 1 0 0 1 1 1c0 1.25.2 2.45.57 3.57a1 1 0 0 1-.25 1z"/></svg>
      <span>01483 556172</span>
    </div>
  </section>

</body>
</html>
```